A start-up named "lumerova" - a clinical research organization needs a new PowerPoint design

We need a new PowerPoint Design (incl. business card and stationery design) for an early-stage start-up named "lumerova" seeking to build an ecosystem/ strategic partner alliances or consortium of committed and active collaborators to guide important components of the clinical trial.

Our ultimate goal is to avoid false neutrals – therapies that have not been and may never be evaluated in clinical trials due to the costs and/ or complexity.

The final design should highlight our patient-centric approach, innovative study design supported with the novel AI platform to make a stronger impact on patient lives.

Please see the attached brief for more details.
Updates

Requesting the proposals on color-coding, business-card designs, clinical research visuals, and icons as well as stationery design.

Target Market(s)

Pharma/ Biotech Executives
Medical Institutions
Clinical Trial Participants (Patients)

Colors
e34398

Requirements
Must have
• Use the Color Version of purple/ magenta logo

```html
<!DOCTYPE html>
<html lang="en">
<head>
<meta charset="utf-8">
<title>lumerova – business cards and letterhead</title>
<link rel="stylesheet" href="https://fonts.googleapis.com/css2?family=Open+Sans:ital,wght@0,400;0,600;0,700;1,400&family=Carlito:ital,wght@0,400;0,700;1,400&family=Great+Vibes&display=swap">
<style>
  :root{
    --magenta:#c4186f;
    --magenta-bright:#e3197f;
    --magenta-deep:#a8155f;
    --ink:#111111;
    --text:#222222;
    --muted:#555555;
    --paper:#ffffff;
    --canvas:#ffffff;
    --stage:#eceef1;
    --letter-top:#e9ebee;
    --letter-bottom:#f9fafb;
  }
  *{box-sizing:border-box;margin:0;padding:0}
  html,body{width:1200px;height:3456px;overflow:hidden;background:var(--canvas)}
  body{position:relative;font-family:"Open Sans",Arial,sans-serif;color:var(--text)}

  /* ---------- presentation stage ---------- */
  .stage{position:absolute;left:0;top:0;width:1200px;height:995px;background:var(--stage)}
  .card{position:absolute;width:706px;height:395px;background:var(--paper);box-shadow:0 18px 40px rgba(0,0,0,.16);overflow:hidden}
  .card-back{left:247px;top:300px;background:linear-gradient(135deg,var(--magenta-bright),var(--magenta) 60%,var(--magenta-deep))}
  .card-back .pattern{position:absolute;inset:0;background:linear-gradient(160deg,rgba(255,255,255,.08),rgba(255,255,255,0) 70%)}
  .card-back .wordmark{position:absolute;left:190px;top:152px;color:#fff}
  .card-back .wordmark .mark-square{background:#fff}

  /* ---------- wordmark ---------- */
  .wordmark{display:flex;align-items:flex-start;gap:8px;font-weight:700;font-size:54px;line-height:1;letter-spacing:-1px;color:var(--magenta)}
  .mark-square{width:20px;height:20px;background:var(--magenta);margin-top:2px}

  /* ---------- business cards ---------- */
  .card-option-01{left:70px;top:1084px}
  .card-option-02{left:423px;top:1541px}
  .card .base-band{position:absolute;left:0;bottom:0;width:100%;height:13px;background:linear-gradient(90deg,var(--magenta-deep),var(--magenta-bright))}
  .card .accent-bar{position:absolute;left:0;width:7px;height:58px;background:var(--magenta)}
  .card-option-01 .accent-bar{top:50px}
  .card-option-02 .accent-bar{top:59px}
  .card .decor{position:absolute;left:0;top:0;width:400px;height:382px;background:linear-gradient(135deg,rgba(220,222,225,.55),rgba(235,236,238,.2) 70%,rgba(255,255,255,0))}
  .holder{position:absolute;left:39px}
  .card-option-01 .holder{top:50px}
  .card-option-02 .holder{top:58px}
  .holder-name{font-size:35px;font-weight:700;color:var(--ink);line-height:1.1;letter-spacing:-.2px}
  .holder-role{font-size:19px;color:var(--magenta);margin-top:3px}
  .card .wordmark{position:absolute;left:38px}
  .card-option-01 .wordmark{top:274px}
  .card-option-02 .wordmark{top:268px}

  .contact{position:absolute;left:452px;font-size:14.5px;color:var(--text);line-height:23px}
  .contact-row{position:absolute;left:0;display:flex;gap:13px;white-space:nowrap}
  .contact-row svg{width:18px;height:18px;flex:none;margin-top:2px}
  .contact-row .lines{display:block}

  .option-label{position:absolute;font-size:43px;color:#333;font-weight:400;letter-spacing:.5px}
  .label-01{left:875px;top:1258px}
  .label-02{left:105px;top:1733px}

  /* ---------- letterhead ---------- */
  .letterhead{position:absolute;left:110px;top:2059px;width:1008px;height:1309px;font-family:"Carlito","Calibri",sans-serif;color:var(--ink);background:linear-gradient(180deg,var(--letter-top) 0,#eef0f2 430px,var(--letter-bottom) 431px,#f2f3f5 900px,var(--letter-bottom));box-shadow:0 25px 50px rgba(0,0,0,.18);overflow:hidden}
  .letterhead .wordmark{position:absolute;left:118px;top:160px;font-family:"Open Sans",Arial,sans-serif;font-size:60px}
  .sender{position:absolute;right:138px;top:150px;text-align:right;font-weight:700;font-size:23px;line-height:28px;padding-right:22px}
  .sender::after{content:"";position:absolute;right:-25px;top:4px;width:9px;height:104px;background:var(--magenta)}
  .recipient{position:absolute;left:131px;top:344px;font-weight:700;font-size:22px;line-height:28.5px}
  .letter-date{position:absolute;right:131px;top:490px;font-weight:700;font-size:22px}
  .letter-body{position:absolute;left:131px;top:562px;width:746px;font-size:19.4px;line-height:27.7px;text-align:justify;color:#1a1a1a}
  .letter-body p+p{margin-top:13px}
  .sign-off{position:absolute;left:129px;top:1060px}
  .signature{font-family:"Great Vibes",cursive;font-size:44px;line-height:1;color:var(--ink)}
  .sign-name{font-weight:700;font-size:19px;margin-top:6px}
  .sign-role{font-style:italic;font-size:19px;margin-top:2px}
  .letter-footer{position:absolute;left:0;bottom:0;width:100%;height:32px;background:linear-gradient(90deg,var(--magenta-deep),var(--magenta-bright) 50%,var(--magenta-deep));display:flex;justify-content:center;align-items:center;gap:16px;color:#fff;font-style:italic;font-size:16.5px}
  .letter-footer span{display:flex;align-items:center;gap:7px}
  .letter-footer svg{width:15px;height:15px}
  .letter-footer .sep{opacity:.9}
</style>
</head>
<body>

<svg width="0" height="0" style="position:absolute" aria-hidden="true">
  <defs>
    <symbol id="icon-pin" viewBox="0 0 24 24"><path fill="currentColor" d="M12 2a7 7 0 0 0-7 7c0 5 7 13 7 13s7-8 7-13a7 7 0 0 0-7-7zm0 9.5A2.5 2.5 0 1 1 12 6.5a2.5 2.5 0 0 1 0 5z"/></symbol>
    <symbol id="icon-mail" viewBox="0 0 24 24"><path fill="currentColor" d="M2 5h20v14H2z"/><path d="M2.5 5.5 12 13l9.5-7.5" fill="none" stroke="#fff" stroke-width="1.6"/></symbol>
    <symbol id="icon-globe" viewBox="0 0 24 24"><g fill="none" stroke="currentColor" stroke-width="1.8"><circle cx="12" cy="12" r="9"/><ellipse cx="12" cy="12" rx="4" ry="9"/><path d="M3 12h18M5 7h14M5 17h14"/></g></symbol>
    <symbol id="icon-phone" viewBox="0 0 24 24"><path fill="currentColor" d="M6.6 2.5 9.5 6 7.8 8.4c1.2 2.9 3.4 5.1 6.3 6.5l2.3-1.8 3.6 2.8-1.5 3.8c-.4.8-1.3 1.2-2.2 1C9.6 19.2 4.6 14.2 3 7.5c-.2-.9.2-1.8 1-2.2z"/></symbol>
    <symbol id="icon-fax" viewBox="0 0 24 24"><path fill="currentColor" d="M7 2h10v6H7zM3 9h18v9h-3v4H6v-4H3zm5 7v4h8v-4z"/></symbol>
  </defs>
</svg>

<!-- card back, shown flat -->
<section class="stage">
  <div class="card card-back">
    <div class="pattern" role="img" aria-label="Faint tonal square pattern across the magenta card back"></div>
    <div class="wordmark">lumerova<span class="mark-square"></span></div>
  </div>
</section>

<!-- business card, option 01 -->
<article class="card card-option-01">
  <div class="decor" role="img" aria-label="Faint grey decorative squares in the background"></div>
  <span class="accent-bar"></span>
  <div class="holder">
    <div class="holder-name">Name Surname, PhD</div>
    <div class="holder-role">Managing Partner</div>
  </div>
  <div class="wordmark">lumerova<span class="mark-square"></span></div>
  <div class="contact" style="color:var(--text)">
    <div class="contact-row" style="top:51px"><svg style="color:var(--magenta)"><use href="#icon-pin"/></svg><span class="lines">Lumerova GmbH<br>Street name 1<br>9999 City name<br>Switzerland</span></div>
    <div class="contact-row" style="top:164px"><svg style="color:var(--magenta)"><use href="#icon-mail"/></svg><span>name.surname@lumerova.ch</span></div>
    <div class="contact-row" style="top:189px"><svg style="color:var(--magenta)"><use href="#icon-globe"/></svg><span>www.lumerova.ch</span></div>
    <div class="contact-row" style="top:234px"><svg style="color:var(--magenta)"><use href="#icon-phone"/></svg><span>Office: +41 (0)12 345 60 00</span></div>
    <div class="contact-row" style="top:259px"><svg style="color:var(--magenta)"><use href="#icon-phone"/></svg><span>Phone: +41 (0)12 345 67 89</span></div>
    <div class="contact-row" style="top:284px"><svg style="color:var(--magenta)"><use href="#icon-phone"/></svg><span>Mobile: +41 (0)98 765 43 21</span></div>
    <div class="contact-row" style="top:309px"><svg style="color:var(--magenta)"><use href="#icon-fax"/></svg><span>Fax: +41 (0)12 345 60 01</span></div>
  </div>
  <span class="base-band"></span>
</article>
<div class="option-label label-01">Option 01</div>

<!-- business card, option 02 -->
<div class="option-label label-02">Option 02</div>
<article class="card card-option-02">
  <span class="accent-bar"></span>
  <div class="holder">
    <div class="holder-name">Name Surname, PhD</div>
    <div class="holder-role">Managing Partner</div>
  </div>
  <div class="wordmark">lumerova<span class="mark-square"></span></div>
  <div class="contact">
    <div class="contact-row" style="top:55px"><svg style="color:var(--magenta)"><use href="#icon-mail"/></svg><span>name.surname@lumerova.ch</span></div>
    <div class="contact-row" style="top:80px"><svg style="color:var(--magenta)"><use href="#icon-globe"/></svg><span>www.lumerova.ch</span></div>
    <div class="contact-row" style="top:133px"><svg style="color:var(--magenta)"><use href="#icon-pin"/></svg><span class="lines">Lumerova GmbH<br>Street name 1<br>9999 City name<br>Switzerland</span></div>
    <div class="contact-row" style="top:243px"><svg style="color:var(--magenta)"><use href="#icon-phone"/></svg><span>Office: +41 (0)12 345 60 00</span></div>
    <div class="contact-row" style="top:268px"><svg style="color:var(--magenta)"><use href="#icon-phone"/></svg><span>Phone: +41 (0)12 345 67 89</span></div>
    <div class="contact-row" style="top:293px"><svg style="color:var(--magenta)"><use href="#icon-phone"/></svg><span>Mobile: +41 (0)98 765 43 21</span></div>
    <div class="contact-row" style="top:318px"><svg style="color:var(--magenta)"><use href="#icon-fax"/></svg><span>Fax: +41 (0)12 345 60 01</span></div>
  </div>
  <span class="base-band"></span>
</article>

<!-- letterhead -->
<article class="letterhead">
  <div class="wordmark">lumerova<span class="mark-square"></span></div>
  <address class="sender" style="font-style:normal">Lumerova GmbH<br>Street name 1<br>9999 City name<br>Switzerland</address>

  <address class="recipient" style="font-style:normal">Name Surname<br>Position<br>Company Name<br>Street name 1<br>9999 City name</address>

  <div class="letter-date">Date: January 2nd, 2021</div>

  <div class="letter-body">
    <p>Lorem ipsum dolor sit amet, consectetuer adipiscing elit, sed diam nonummy nibh euismod tincidunt ut laoreet dolore magna aliquam erat volutpat. Ut wisi enim ad minim veniam, quis nostrud exerci tation ullamcorper suscipit lobortis nisl ut aliquip ex ea commodo consequat. Duis autem vel eum iriure dolor in hendrerit in vulputate velit esse molestie consequat, vel illum dolore eu feugiat nulla facilisis at vero eros et accumsan et iusto odio dignissim qui blandit praesent luptatum zzril delenit augue duis dolore te feugait nulla facilisi.</p>
    <p>Porem ipsum dolor sit amet, cons ectetuer adipiscing elit, sed diam nonummy nibh euismod tincidunt ut laoreet dolore magna aliquam erat volutpat. Ut wisi enim ad minim veniam, quis nostrud exerci tation.</p>
    <p>Lorem ipsum dolor sit amet, cons ectetuer adipiscing elit, sed diam nonummy nibh euismod tincidunt ut laoreet dolore magna aliquam erat volutpat. Ut wisi enim ad minim veniam, quis nostrud exerci tation ullamcorper suscipit lobortis nisl ut aliquip ex ea commodo consequat. Lorem ipsum dolor sit amet, cons ectetuer adipiscing elit, sed diam nonummy nibh euismod tincidunt ut laoreet dolore.</p>
  </div>

  <div class="sign-off">
    <div class="signature">Signature</div>
    <div class="sign-name">Name Surname</div>
    <div class="sign-role">Position</div>
  </div>

  <footer class="letter-footer">
    <span><svg><use href="#icon-globe"/></svg>www.lumerova.ch</span>
    <span class="sep">|</span>
    <span><svg><use href="#icon-mail"/></svg>name.surname@lumerova.ch</span>
    <span class="sep">|</span>
    <span><svg><use href="#icon-phone"/></svg>+41 (0)12 345 60 00</span>
  </footer>
</article>

</body>
</html>
```